Modular Cat Home Business Card

We need a business card for a modular and configurable cat playhouse, known as NookBox. NookBoxes can be integrated with human furniture. They come in cubes that are stackable, customizable and interchangeable.

Our name card should be in the shape of an isometric cube (not a normal business card size) with the NookBox logo inside the cube on one side of the namecard. If a home can be created inside the cube to show a homely environment, that could be an option. We are toying with the idea of having the cube side black and white and the flip side with our details, colorful. Our brand colours are pastel. They include pastel yellow, pink, purple, blue and orange. On the flip side, should be details including our name, position, email address, website, contact number.

The overall design should be clean, minimalistic, yet portray fun, happiness and quirky style. The product is design oriented so the name card should reflect likewise.

Target Market(s)

Cat Owners, Home owners, Mid 20s

Industry/Entity Type

Business

Contact Information for Business Card

Name, position, company name, phone number, email address, website. Name font should be bigger.

Colors
f8ba93
f9d9e8
ecdaeb
cee9f5
cfeae6
eaf2ce
fcf9cd
fce8d3
fbd4d5

Requirements
Must have
• The logo
• A variety of pastel colors
• A die cut in the form of a cube
Nice to have
• A home in the cube, to show furniture integration

```html
<!DOCTYPE html>
<html lang="en">
<head>
<meta charset="utf-8">
<title>NookBox Cube Card – Top, Bottom and Sides</title>
<link rel="stylesheet" href="https://fonts.googleapis.com/css2?family=Jost:wght@400;500;700&display=swap">
<style>
  :root {
    --backdrop: #8a5a3b;
    --card-light: #3c3c3c;
    --card-dark: #050505;
    --grid-line: #000000;
    --grid-highlight: #ffffff;
    --disc: #ffffff;
    --ink: #000000;
    --ink-soft: #2e2e2e;
    --ink-muted: #6b6b6b;
    --label: #ffffff;
    --pastel-pink: #f9d9e8;
    --pastel-blue: #cee9f5;
    --pastel-peach: #fce8d3;
    --pastel-mint: #cfeae6;
    --side-grid: rgba(255,255,255,0.55);
    --side-ring: #e9e9e9;
  }
  * { margin: 0; padding: 0; box-sizing: border-box; }
  html, body { width: 1200px; height: 960px; overflow: hidden; }
  body {
    background: var(--backdrop);
    font-family: "Jost", "Helvetica Neue", Arial, sans-serif;
    position: relative;
  }
  .card-face {
    position: absolute;
    top: 100px;
    width: 342px;
    height: 343px;
    box-shadow: 4px 6px 10px rgba(0,0,0,0.45);
  }
  .card-face--top { left: 200px; }
  .card-face--bottom { left: 632px; }
  .card-face svg { display: block; }
  .face-label {
    position: absolute;
    top: 468px;
    width: 342px;
    text-align: center;
    color: var(--label);
    font-weight: 700;
    font-size: 16px;
    letter-spacing: 0.5px;
  }
  .face-label--top { left: 200px; }
  .face-label--bottom { left: 632px; }
  .disc-content {
    position: absolute;
    left: 46px; top: 46px;
    width: 250px; height: 250px;
    border-radius: 50%;
    display: flex; flex-direction: column; align-items: center;
    text-align: center;
  }
  .brand-frame {
    margin-top: 56px;
    width: 92px; height: 92px;
    border: 3px solid var(--ink);
  }
  .brand-name {
    margin-top: 16px;
    font-size: 15px;
    font-weight: 400;
    letter-spacing: 6px;
    color: var(--ink-muted);
  }
  .contact-mark {
    margin-top: 52px;
    width: 38px; height: 38px;
    border-radius: 50%;
    background: var(--ink);
  }
  .person-name {
    margin-top: 14px;
    font-size: 30px;
    font-weight: 700;
    line-height: 1;
    color: var(--ink);
  }
  .person-role {
    margin-top: 3px;
    font-size: 16px;
    font-weight: 400;
    color: var(--ink);
  }
  .contact-list {
    list-style: none;
    margin-top: 12px;
    font-size: 13px;
    line-height: 16px;
    color: var(--ink-soft);
  }
  .side-row {
    position: absolute;
    left: 100px; top: 580px;
    display: flex; gap: 40px;
  }
  .side-face {
    width: 220px; height: 220px;
    box-shadow: 4px 6px 10px rgba(0,0,0,0.4);
  }
  .side-face svg { display: block; }
</style>
</head>
<body>

<svg width="0" height="0" style="position:absolute">
  <defs>
    <linearGradient id="card-shade" x1="0" y1="0" x2="1" y2="0">
      <stop offset="0" stop-color="var(--card-light)"/>
      <stop offset="1" stop-color="var(--card-dark)"/>
    </linearGradient>
    <linearGradient id="scene-shelf" x1="0" y1="0" x2="1" y2="1">
      <stop offset="0" stop-color="#9cc9d6"/><stop offset="1" stop-color="#3f8f8a"/>
    </linearGradient>
    <linearGradient id="scene-window" x1="0" y1="0" x2="0" y2="1">
      <stop offset="0" stop-color="#c9ccd0"/><stop offset="1" stop-color="#f4f4f4"/>
    </linearGradient>
    <linearGradient id="scene-cube" x1="0" y1="0" x2="1" y2="0">
      <stop offset="0" stop-color="#5b8fb5"/><stop offset="1" stop-color="#c9823f"/>
    </linearGradient>
    <linearGradient id="scene-lounge" x1="0" y1="0" x2="0" y2="1">
      <stop offset="0" stop-color="#e7e2d6"/><stop offset="0.5" stop-color="#e3b84a"/><stop offset="1" stop-color="#3e6f5e"/>
    </linearGradient>
    <g id="card-base">
      <rect width="342" height="343" fill="url(#card-shade)"/>
      <g stroke="var(--grid-line)" stroke-width="4">
        <line x1="35" y1="0" x2="35" y2="343"/>
        <line x1="105" y1="0" x2="105" y2="343"/>
        <line x1="175" y1="0" x2="175" y2="343"/>
        <line x1="245" y1="0" x2="245" y2="343"/>
        <line x1="307" y1="0" x2="307" y2="343"/>
        <line x1="0" y1="36" x2="342" y2="36"/>
        <line x1="0" y1="104" x2="342" y2="104"/>
        <line x1="0" y1="172" x2="342" y2="172"/>
        <line x1="0" y1="240" x2="342" y2="240"/>
        <line x1="0" y1="308" x2="342" y2="308"/>
      </g>
      <g stroke="var(--grid-highlight)" stroke-width="2">
        <line x1="28" y1="0" x2="28" y2="343"/>
        <line x1="314" y1="0" x2="314" y2="343"/>
        <line x1="0" y1="28" x2="342" y2="28"/>
        <line x1="0" y1="314" x2="342" y2="314"/>
      </g>
      <g fill="var(--disc)" stroke="var(--ink)" stroke-width="3">
        <circle cx="30" cy="30" r="14"/>
        <circle cx="310" cy="30" r="14"/>
        <circle cx="30" cy="311" r="14"/>
        <circle cx="310" cy="311" r="14"/>
      </g>
      <circle cx="171" cy="171" r="126" fill="var(--disc)" stroke="var(--ink)" stroke-width="4"/>
    </g>
    <g id="side-frame">
      <g stroke="var(--side-grid)" stroke-width="2">
        <line x1="55" y1="0" x2="55" y2="220"/>
        <line x1="110" y1="0" x2="110" y2="220"/>
        <line x1="165" y1="0" x2="165" y2="220"/>
        <line x1="0" y1="55" x2="220" y2="55"/>
        <line x1="0" y1="110" x2="220" y2="110"/>
        <line x1="0" y1="165" x2="220" y2="165"/>
      </g>
      <g fill="var(--disc)">
        <circle cx="16" cy="16" r="7"/>
        <circle cx="204" cy="16" r="7"/>
        <circle cx="16" cy="204" r="7"/>
        <circle cx="204" cy="204" r="7"/>
      </g>
      <circle cx="110" cy="110" r="80" fill="var(--side-ring)"/>
    </g>
  </defs>
</svg>

<section class="card-face card-face--top" aria-label="Card top face">
  <svg width="342" height="343" viewBox="0 0 342 343"><use href="#card-base"/></svg>
  <div class="disc-content">
    <div class="brand-frame"></div>
    <p class="brand-name">NOOKBOX</p>
  </div>
</section>

<section class="card-face card-face--bottom" aria-label="Card bottom face">
  <svg width="342" height="343" viewBox="0 0 342 343"><use href="#card-base"/></svg>
  <div class="disc-content">
    <div class="contact-mark"></div>
    <h1 class="person-name">JAMIE ROWE</h1>
    <p class="person-role">CEO/FOUNDER</p>
    <ul class="contact-list">
      <li>555- 214-0387</li>
      <li>hello@nookboxes.com</li>
      <li>www.nookboxes.com</li>
    </ul>
  </div>
</section>

<p class="face-label face-label--top">TOP</p>
<p class="face-label face-label--bottom">BOTTOM</p>

<div class="side-row" aria-label="Cube side faces">
  <section class="side-face" aria-label="Pink side">
    <svg width="220" height="220" viewBox="0 0 220 220">
      <rect width="220" height="220" fill="var(--pastel-pink)"/>
      <use href="#side-frame"/>
      <circle cx="110" cy="110" r="68" fill="url(#scene-shelf)" role="img" aria-label="Photo of stacked cat cubes beside a potted plant"/>
    </svg>
  </section>
  <section class="side-face" aria-label="Blue side">
    <svg width="220" height="220" viewBox="0 0 220 220">
      <rect width="220" height="220" fill="var(--pastel-blue)"/>
      <use href="#side-frame"/>
      <circle cx="110" cy="110" r="68" fill="url(#scene-window)" role="img" aria-label="Photo of a room with curtains and cat cube seating"/>
    </svg>
  </section>
  <section class="side-face" aria-label="Peach side">
    <svg width="220" height="220" viewBox="0 0 220 220">
      <rect width="220" height="220" fill="var(--pastel-peach)"/>
      <use href="#side-frame"/>
      <circle cx="110" cy="110" r="68" fill="url(#scene-cube)" role="img" aria-label="Photo of a colourful modular cat cube"/>
    </svg>
  </section>
  <section class="side-face" aria-label="Mint side">
    <svg width="220" height="220" viewBox="0 0 220 220">
      <rect width="220" height="220" fill="var(--pastel-mint)"/>
      <use href="#side-frame"/>
      <circle cx="110" cy="110" r="68" fill="url(#scene-lounge)" role="img" aria-label="Photo of a lounge with a sofa and cat cubes built into furniture"/>
    </svg>
  </section>
</div>

</body>
</html>
```